Seeking a new website design for electrical contracting company

Brisket & Vane electrical contracting needs a new website for brisket-vane.example

We are looking for modern and something real cool with motion for a landing page. we have some cool images from our photo shoot. maybe even 3d motion our existing logo. we would like something we can edit with news and events and update a past project page. Also allow to take payment
stock images at
https://lorapellwinphotos.picvault-demo.example/Brisket-and-Vane

Target Market(s)

construction , home owners , business owners,

Industry/Entity Type

construction , electrical

Coding

Number of Pages Required

5+ page

Font styles to use
Serif
Sans Serif

Colors
0054AA
0677BA
7BADD7
CADEEF
E8F1F8
0094D4
00A9DD
6FCCEA
C7EBF8
E9F6FB
FFF300
FFF600
FEFA6F
FFFEC7
FFFEE8

Requirements
Must have
• excitement, motion, selling professionalism,

```html
<!DOCTYPE html>
<html lang="en">
<head>
<meta charset="utf-8">
<title>Brisket &amp; Vane Electrical Contracting</title>
<link rel="stylesheet" href="https://fonts.googleapis.com/css2?family=Outfit:wght@400;500;600;700;800&family=Figtree:wght@400;500;600;700&display=swap">
<style>
:root{
  --navy:#272c72;
  --navy-dark:#1f235e;
  --royal:#3b3fd6;
  --orange:#f4911e;
  --ink:#2b2d5e;
  --text:#44475a;
  --panel:#f2f2f2;
  --footer:#1b1b1d;
  --white:#ffffff;
}
*{box-sizing:border-box;margin:0;padding:0}
html,body{width:1200px;height:4743px;overflow:hidden;background:var(--white)}
body{position:relative;font-family:"Figtree",sans-serif;color:var(--text)}
.abs{position:absolute}
.accent{color:var(--orange)}

/* hero */
.hero{left:0;top:0;width:1200px;height:736px;clip-path:polygon(0 0,100% 0,100% 653px,50% 736px,0 653px);
  background:
    radial-gradient(ellipse 420px 360px at 160px 260px,rgba(20,22,90,.55),rgba(20,22,90,0)),
    radial-gradient(ellipse 380px 340px at 1040px 300px,rgba(18,20,80,.5),rgba(18,20,80,0)),
    radial-gradient(ellipse 300px 260px at 760px 240px,rgba(120,130,255,.35),rgba(120,130,255,0)),
    linear-gradient(165deg,#4f55ee 0%,#3a3fd0 45%,#2a2ea6 75%,#1d1f78 100%)}
.topbar{top:28px;font-size:15px;color:var(--white);display:flex;align-items:center;gap:8px}
.nav-rule{top:77px;height:1px;background:rgba(255,255,255,.45)}
.nav{top:100px;display:flex;gap:34px;font-family:"Outfit",sans-serif;font-weight:600;font-size:14px;color:var(--white);letter-spacing:.3px}
.brand{text-align:center;font-family:"Outfit",sans-serif;font-weight:700;color:var(--white)}
.brand-mark{display:inline-block;width:40px;height:40px;border:3px solid var(--white);border-radius:50%}
.brand-name{font-size:26px;letter-spacing:.5px;line-height:1}
.brand-tag{font-size:9px;letter-spacing:2px;color:var(--orange);font-weight:600}
.hero-title{left:0;width:1200px;top:262px;text-align:center;color:var(--white);font-family:"Outfit",sans-serif;font-weight:800;font-size:76px;line-height:1}
.hero-sub{left:0;width:1200px;top:334px;text-align:center;color:var(--white);font-family:"Outfit",sans-serif;font-weight:500;font-size:48px;line-height:1}
.hero-copy{left:290px;width:620px;top:392px;text-align:center;color:var(--white);font-size:22px;line-height:31px}
.btn-solid{background:var(--orange);color:var(--white);font-family:"Outfit",sans-serif;font-weight:600;font-size:15px;display:flex;align-items:center;justify-content:center;letter-spacing:.5px}
.btn-line{border:2px solid var(--orange);color:var(--orange);font-family:"Outfit",sans-serif;font-weight:600;font-size:15px;display:flex;align-items:center;justify-content:center;letter-spacing:.5px}

.sec-title{font-family:"Outfit",sans-serif;font-weight:600;font-size:39px;color:var(--ink);line-height:1;letter-spacing:.5px}
.sec-copy{font-size:20px;line-height:27px;color:var(--text)}

/* services */
.tabs{left:74px;top:952px;width:1052px;display:flex;justify-content:space-between;padding:0 30px;font-size:15px;font-weight:600;color:var(--ink)}
.tab-rule{left:74px;top:990px;width:1052px;height:1px;background:#9a9cc2}
.tab-active-rule{left:74px;top:988px;width:210px;height:4px;background:var(--orange)}
.panel{left:74px;top:1047px;width:1052px;height:453px;background:var(--panel)}
.panel-shadow{left:130px;top:1500px;width:958px;height:14px;background:linear-gradient(#d6d6d6,#fff)}
.panel-title{left:125px;top:1087px;font-family:"Outfit",sans-serif;font-weight:600;font-size:25px;color:var(--ink)}
.checklist{left:125px;top:1128px;list-style:none;font-size:17px;color:var(--ink)}
.checklist li{height:33.7px;display:flex;align-items:center;gap:12px}
.diamond{width:46px;height:46px;transform:rotate(45deg);display:flex;align-items:center;justify-content:center}
.diamond svg{transform:rotate(-45deg)}

/* about */
.about{left:0;top:1586px;width:1200px;height:445px;background:linear-gradient(100deg,#2a2f7a 50%,#1f235e 100%)}
.about-photo{left:0;top:1586px;width:640px;height:445px;clip-path:polygon(0 0,585px 0,640px 445px,0 445px);
  background:
    radial-gradient(ellipse 120px 90px at 410px 70px,rgba(246,196,40,.85),rgba(246,196,40,0)),
    radial-gradient(ellipse 170px 200px at 420px 220px,rgba(214,160,120,.55),rgba(214,160,120,0)),
    radial-gradient(ellipse 200px 150px at 420px 420px,rgba(40,60,120,.8),rgba(40,60,120,0)),
    linear-gradient(110deg,#3f4a58 0%,#56616e 35%,#6d6a66 65%,#8a6a46 100%)}
.about-title{left:615px;top:1645px;font-family:"Outfit",sans-serif;font-weight:600;font-size:38px;color:var(--white);line-height:1}
.about-sub{left:615px;top:1684px;font-family:"Outfit",sans-serif;font-weight:500;font-size:28px;color:var(--orange);line-height:1}
.about-copy{left:615px;top:1724px;width:515px;font-size:17px;line-height:29px;color:#e6e7f3}

/* testimonial */
.quote-band{left:340px;top:2883px;width:860px;height:306px;background:var(--navy)}
.quote-text{left:478px;top:2938px;width:640px;font-size:18px;line-height:29px;color:#e6e7f3}
.quote-mark{left:470px;top:2905px;font-family:"Outfit",sans-serif;font-size:70px;color:#7b7fa8;line-height:1}
.avatar{left:478px;top:3085px;width:72px;height:72px;background:linear-gradient(#c9ccd2,#3e4150);clip-path:polygon(25% 0,75% 0,100% 50%,75% 100%,25% 100%,0 50%)}
.quote-name{left:567px;top:3093px;font-family:"Outfit",sans-serif;font-weight:600;font-size:20px;color:var(--white)}
.quote-role{left:567px;top:3121px;font-size:15px;color:var(--orange)}

/* news */
.card{top:3389px;width:328px;height:367px;border-radius:8px;overflow:hidden}
.card-fill{position:absolute;inset:0}
.card-shade{position:absolute;inset:0;background:linear-gradient(rgba(39,44,114,0) 45%,rgba(39,44,114,.95) 85%)}
.card-badge{position:absolute;left:22px;top:210px;width:62px;height:70px;background:var(--orange);clip-path:polygon(50% 0,100% 25%,100% 75%,50% 100%,0 75%,0 25%);color:var(--white);text-align:center;font-family:"Outfit",sans-serif}
.card-badge small{display:block;font-size:10px;font-weight:600;margin-top:13px;line-height:1}
.card-badge b{display:block;font-size:30px;line-height:1;font-weight:600}
.card-title{position:absolute;left:20px;top:290px;width:290px;font-family:"Outfit",sans-serif;font-weight:500;font-size:23px;line-height:28px;color:var(--white)}

/* contact */
.map{left:420px;top:3873px;width:780px;height:429px;background:
  radial-gradient(ellipse 260px 200px at 360px 210px,#e4e5ee,rgba(228,229,238,0)),
  linear-gradient(90deg,#d6d7e2 0%,#dfe0e9 70%,#cfd6ea 85%,#d6d7e2 100%)}
.contact-hex{left:0;top:3836px;width:536px;height:499px;background:var(--orange);clip-path:polygon(25% 0,75% 0,100% 50%,75% 100%,25% 100%,0 50%)}
.contact-info{left:0;width:494px;text-align:center;color:var(--white)}

/* footer */
.footer{left:0;top:4409px;width:1200px;height:334px;background:var(--footer)}
.foot-col{top:4466px;font-size:13px;color:#d8d8dc;line-height:32px}
.foot-col h4{font-family:"Outfit",sans-serif;font-weight:500;font-size:15px;color:var(--orange);letter-spacing:.5px;line-height:22px;margin-bottom:4px}
.social{left:883px;top:4636px;display:flex;gap:14px}
.social span{width:20px;height:20px;border-radius:50%;background:#e2e2e6;display:block}
</style>
</head>
<body>

<section class="abs hero" role="img" aria-label="Photo of electricians in hard hats working at an electrical panel, tinted blue"></section>

<div class="abs topbar" style="left:74px">
  <svg width="16" height="14" viewBox="0 0 16 14"><path d="M1 2l4-1.5 6 2 4-1.5v11l-4 1.5-6-2-4 1.5z" fill="#f4911e"/></svg>
  12 Alder Row, Kettleford NH 03000
</div>
<div class="abs topbar" style="left:762px">
  <svg width="14" height="14" viewBox="0 0 14 14"><path d="M3 1l2.5 3-1.5 1.5c1 2 2.5 3.5 4.5 4.5L10 8.5l3 2.5-1.5 2.5C6 13 1 8 .5 2.5z" fill="#f4911e"/></svg>
  1-555-014-2290
  <svg width="16" height="12" viewBox="0 0 16 12" style="margin-left:14px"><rect width="16" height="12" rx="1" fill="#f4911e"/><path d="M1 1l7 5 7-5" stroke="#3438c4" stroke-width="1.5" fill="none"/></svg>
  hello@brisket-vane.example
</div>

<div class="abs nav-rule" style="left:74px;width:358px"></div>
<div class="abs nav-rule" style="left:768px;width:358px"></div>
<nav class="abs nav" style="left:74px;align-items:center">
  <svg width="16" height="14" viewBox="0 0 16 14"><path d="M8 0l8 7h-2v7H10V9H6v5H2V7H0z" fill="#f4911e"/></svg>
  <span>ABOUT US</span><span>SERVICES</span><span>PROJECTS</span>
</nav>
<nav class="abs nav" style="left:850px"><span>NEWS AND EVENTS</span><span>CONTACT US</span></nav>

<div class="abs brand" style="left:450px;width:300px;top:20px">
  <span class="brand-mark"></span>
  <div class="brand-name" style="margin-top:8px">BRISKET &amp; VANE</div>
  <div class="brand-tag" style="margin-top:4px">ELECTRICAL CONTRACTORS</div>
</div>

<h1 class="abs hero-title">Brisket &amp; Vane</h1>
<div class="abs hero-sub">Electrical Contracting</div>
<p class="abs hero-copy">Excepteur sint occaecat cupidatat non proident, sunt in culpa qui officia deserunt mollit anim.</p>
<a class="abs btn-solid" style="left:510px;top:482px;width:180px;height:46px">CONTACT US</a>

<svg class="abs" style="left:588px;top:684px" width="24" height="26" viewBox="0 0 24 26"><path d="M12 2v20M3 14l9 9 9-9" stroke="#ffffff" stroke-width="3" fill="none"/></svg>

<!-- SERVICES -->
<h2 class="abs sec-title" style="left:0;width:1200px;text-align:center;top:809px">SERVICES <span class="accent">WE</span> OFFERS</h2>
<p class="abs sec-copy" style="left:300px;width:600px;text-align:center;top:860px">Duis aute irure dolor in reprehenderit in voluptate velit esse cillum dolore eu fugiat nulla pariatur.</p>

<div class="abs tabs">
  <span style="color:var(--orange)">Residential Services</span>
  <span>Commercial Services</span>
  <span>Industrial Services</span>
  <span>Design &amp; Installation</span>
  <span>Maintenance &amp; Support</span>
</div>
<div class="abs tab-rule"></div>
<div class="abs tab-active-rule"></div>

<div class="abs panel-shadow"></div>
<div class="abs panel"></div>
<h3 class="abs panel-title">RESIDENTIAL ELECTRICAL SERVICES</h3>
<ul class="abs checklist">
  <li><svg width="16" height="12" viewBox="0 0 16 12"><path d="M1 6l5 5L15 1" stroke="#f4911e" stroke-width="3" fill="none"/></svg>New Home Wiring &amp; Installations</li>
  <li><svg width="16" height="12" viewBox="0 0 16 12"><path d="M1 6l5 5L15 1" stroke="#f4911e" stroke-width="3" fill="none"/></svg>Electrical Panel Upgrades</li>
  <li><svg width="16" height="12" viewBox="0 0 16 12"><path d="M1 6l5 5L15 1" stroke="#f4911e" stroke-width="3" fill="none"/></svg>Lighting Design &amp; Installation (Interior/Exterior)</li>
  <li><svg width="16" height="12" viewBox="0 0 16 12"><path d="M1 6l5 5L15 1" stroke="#f4911e" stroke-width="3" fill="none"/></svg>Home Automation &amp; Smart Home Setup</li>
  <li><svg width="16" height="12" viewBox="0 0 16 12"><path d="M1 6l5 5L15 1" stroke="#f4911e" stroke-width="3" fill="none"/></svg>Ceiling Fan &amp; Appliance Wiring</li>
  <li><svg width="16" height="12" viewBox="0 0 16 12"><path d="M1 6l5 5L15 1" stroke="#f4911e" stroke-width="3" fill="none"/></svg>EV Charger Installation</li>
  <li><svg width="16" height="12" viewBox="0 0 16 12"><path d="M1 6l5 5L15 1" stroke="#f4911e" stroke-width="3" fill="none"/></svg>Surge Protection</li>
  <li><svg width="16" height="12" viewBox="0 0 16 12"><path d="M1 6l5 5L15 1" stroke="#f4911e" stroke-width="3" fill="none"/></svg>Troubleshooting &amp; Repairs</li>
</ul>

<svg class="abs" style="left:630px;top:1068px" width="440" height="412" viewBox="0 0 440 412">
  <defs>
    <linearGradient id="kitchen" x1="0" y1="0" x2="1" y2="1"><stop offset="0" stop-color="#efe4cf"/><stop offset=".45" stop-color="#d9c4a0"/><stop offset=".75" stop-color="#5b6c92"/><stop offset="1" stop-color="#8a6a48"/></linearGradient>
    <linearGradient id="house" x1="0" y1="0" x2="0" y2="1"><stop offset="0" stop-color="#2c4a86"/><stop offset=".5" stop-color="#7f93bb"/><stop offset=".7" stop-color="#e8d7b0"/><stop offset="1" stop-color="#3f6a35"/></linearGradient>
  </defs>
  <polygon role="img" aria-label="Photo of an electrician installing pendant lights in a kitchen" points="257,0 437,101 437,303 257,404 77,303 77,101" fill="url(#kitchen)"/>
  <polygon role="img" aria-label="Photo of a modern house at dusk" points="100,190 195,243 195,349 100,402 5,349 5,243" fill="url(#house)"/>
</svg>

<div class="abs diamond" style="left:51px;top:1248px;background:var(--navy)"><svg width="14" height="18" viewBox="0 0 14 18"><path d="M10 2L3 9l7 7" stroke="#fff" stroke-width="2.5" fill="none"/></svg></div>
<div class="abs diamond" style="left:1101px;top:1248px;background:var(--orange)"><svg width="14" height="18" viewBox="0 0 14 18"><path d="M4 2l7 7-7 7" stroke="#fff" stroke-width="2.5" fill="none"/></svg></div>

<!-- ABOUT -->
<section class="abs about"></section>
<div class="abs about-photo" role="img" aria-label="Photo of a smiling electrician in a yellow hard hat working at a breaker panel"></div>
<h2 class="abs about-title">ABOUT BRISKET &amp; VANE</h2>
<div class="abs about-sub">ELECTRICAL CONTRACTING</div>
<p class="abs about-copy">Nemo enim ipsam voluptatem quia voluptas sit aspernatur aut odit aut fugit, sed quia consequuntur magni dolores eos qui ratione voluptatem sequi nesciunt. Neque porro quisquam est, qui dolorem ipsum quia dolor sit amet, consectetur, adipisci velit, sed quia non numquam eius modi tempora incidunt ut labore et dolore magnam.</p>
<a class="abs btn-line" style="left:615px;top:1919px;width:180px;height:50px">READ MORE</a>

<!-- PROJECTS -->
<h2 class="abs sec-title" style="left:74px;top:2090px">OUR <span class="accent">PAST</span> PROJECTS</h2>
<p class="abs sec-copy" style="left:74px;width:580px;top:2139px">Duis aute irure dolor in reprehenderit in voluptate velit esse cillum dolore eu fugiat nulla pariatur.</p>
<a class="abs btn-line" style="left:929px;top:2120px;width:197px;height:49px">VIEW ALL PROJECTS</a>

<svg class="abs" style="left:0;top:2232px" width="1200" height="560" viewBox="0 0 1200 560">
  <defs>
    <linearGradient id="p1" x1="0" y1="0" x2="1" y2="1"><stop offset="0" stop-color="#f0f0f2"/><stop offset=".5" stop-color="#d9d4cc"/><stop offset="1" stop-color="#9c8c78"/></linearGradient>
    <linearGradient id="p2" x1="0" y1="0" x2="1" y2="1"><stop offset="0" stop-color="#e6dfd4"/><stop offset=".5" stop-color="#a89a8a"/><stop offset="1" stop-color="#3e3a38"/></linearGradient>
    <linearGradient id="p3" x1="0" y1="0" x2="1" y2="1"><stop offset="0" stop-color="#a3aab3"/><stop offset=".5" stop-color="#5c6676"/><stop offset="1" stop-color="#243463"/></linearGradient>
    <linearGradient id="p4" x1="0" y1="0" x2="1" y2="1"><stop offset="0" stop-color="#f6f1ea"/><stop offset=".5" stop-color="#d8c4ae"/><stop offset="1" stop-color="#6d5646"/></linearGradient>
    <linearGradient id="p5" x1="0" y1="0" x2="1" y2="1"><stop offset="0" stop-color="#d9c8b0"/><stop offset=".5" stop-color="#a98e72"/><stop offset="1" stop-color="#5a4a3c"/></linearGradient>
    <linearGradient id="p6" x1="0" y1="0" x2="1" y2="1"><stop offset="0" stop-color="#a58a68"/><stop offset=".5" stop-color="#5e5248"/><stop offset="1" stop-color="#2e2f36"/></linearGradient>
    <linearGradient id="p7" x1="0" y1="0" x2="1" y2="1"><stop offset="0" stop-color="#e2e2e6"/><stop offset=".5" stop-color="#6f7fbf"/><stop offset="1" stop-color="#1f2f7a"/></linearGradient>
    <linearGradient id="p8" x1="0" y1="0" x2="1" y2="1"><stop offset="0" stop-color="#efe4cf"/><stop offset=".5" stop-color="#cdb48e"/><stop offset="1" stop-color="#4f6488"/></linearGradient>
  </defs>
  <polygon role="img" aria-label="Photo of an electrician wiring a wall outlet" points="210,0 346,78 346,235 210,313 74,235 74,78" fill="url(#p1)"/>
  <polygon role="img" aria-label="Photo of an electrician fitting a ceiling light" points="495,0 631,78 631,235 495,313 359,235 359,78" fill="url(#p2)"/>
  <polygon role="img" aria-label="Photo of an electrician working on a panel" points="780,0 916,78 916,235 780,313 644,235 644,78" fill="url(#p3)"/>
  <polygon role="img" aria-label="Photo of an electrician installing a recessed light" points="1065,0 1201,78 1201,235 1065,313 929,235 929,78" fill="url(#p4)"/>
  <polygon role="img" aria-label="Photo of an electrician testing a switch" points="67,246 203,324 203,481 67,559 -69,481 -69,324" fill="url(#p5)"/>
  <polygon role="img" aria-label="Photo of an electrician checking a tablet beside a panel" points="352,246 488,324 488,481 352,559 216,481 216,324" fill="url(#p6)"/>
  <polygon role="img" aria-label="Photo of an electrician kneeling at a service cabinet" points="637,246 773,324 773,481 637,559 501,481 501,324" fill="url(#p7)"/>
  <polygon role="img" aria-label="Photo of an electrician hanging pendant lights in a kitchen" points="922,246 1058,324 1058,481 922,559 786,481 786,324" fill="url(#p8)"/>
</svg>

<!-- TESTIMONIAL -->
<div class="abs quote-band"></div>
<div class="abs" role="img" aria-label="Photo of a smiling client in a dark shirt" style="left:74px;top:2883px;width:353px;height:306px;background:radial-gradient(ellipse 90px 110px at 50% 38%,#c9a58a,rgba(201,165,138,0)),linear-gradient(180deg,#d8dadf 0%,#9ea3ae 55%,#3a3f52 100%);clip-path:polygon(25% 0,75% 0,100% 50%,75% 100%,25% 100%,0 50%)"></div>
<div class="abs quote-mark">“</div>
<p class="abs quote-text">Nemo enim ipsam voluptatem quia voluptas sit aspernatur aut odit aut fugit, sed quia consequuntur magni dolores eos qui ratione voluptatem sequi nesciunt. Neque porro quisquam est, qui dolorem ipsum quia dolor sit amet, consectetur, adipisci velit..”</p>
<div class="abs avatar" role="img" aria-label="Client portrait"></div>
<div class="abs quote-name">Name Heading</div>
<div class="abs quote-role">Location</div>
<div class="abs diamond" style="left:1038px;top:3099px;width:28px;height:28px;background:var(--orange)"><svg width="8" height="10" viewBox="0 0 8 10"><path d="M6 1L2 5l4 4" stroke="#fff" stroke-width="1.6" fill="none"/></svg></div>
<div class="abs diamond" style="left:1090px;top:3099px;width:28px;height:28px;background:var(--white)"><svg width="8" height="10" viewBox="0 0 8 10"><path d="M2 1l4 4-4 4" stroke="#272c72" stroke-width="1.6" fill="none"/></svg></div>

<!-- NEWS -->
<h2 class="abs sec-title" style="left:74px;top:3251px">NEWS <span class="accent">AND</span> EVENTS</h2>
<p class="abs sec-copy" style="left:74px;width:580px;top:3302px">Duis aute irure dolor in reprehenderit in voluptate velit esse cillum dolore eu fugiat nulla pariatur.</p>
<a class="abs btn-line" style="left:948px;top:3283px;width:178px;height:49px">VIEW ALL NEWS</a>

<article class="abs card" style="left:74px">
  <div class="card-fill" role="img" aria-label="Photo of an electrician on a ladder in a hard hat" style="background:radial-gradient(ellipse 90px 70px at 80% 22%,#d9a24a,rgba(217,162,74,0)),linear-gradient(135deg,#eeeef0,#c8c2b8 50%,#8a8c9c)"></div>
  <div class="card-shade"></div>
  <div class="card-badge"><small>APR</small><b>20</b></div>
  <h3 class="card-title">Excepteur sint occaecat cupidatat nonpr</h3>
</article>
<article class="abs card" style="left:436px">
  <div class="card-fill" role="img" aria-label="Photo of an electrician testing a breaker panel" style="background:radial-gradient(ellipse 90px 80px at 70% 25%,#e8e8ec,rgba(232,232,236,0)),linear-gradient(135deg,#c9ccd4,#7a8296 50%,#3a4470)"></div>
  <div class="card-shade"></div>
  <div class="card-badge"><small>APR</small><b>20</b></div>
  <h3 class="card-title">Excepteur sint occaecat cupidatat nonpr</h3>
</article>
<article class="abs card" style="left:797px">
  <div class="card-fill" role="img" aria-label="Photo of an empty room under renovation" style="background:linear-gradient(180deg,#f4f4f6,#dcdbe0 45%,#b8a890 75%,#8e8c96)"></div>
  <div class="card-shade"></div>
  <div class="card-badge"><small>APR</small><b>20</b></div>
  <h3 class="card-title">Excepteur sint occaecat cupidatat nonpr</h3>
</article>

<!-- CONTACT -->
<div class="abs map" role="img" aria-label="Street map showing the office location with a pin"></div>
<div class="abs contact-hex"></div>
<div class="abs brand contact-info" style="top:3900px">
  <span class="brand-mark"></span>
  <div class="brand-name" style="font-size:31px;margin-top:22px">BRISKET &amp; VANE</div>
  <div class="brand-tag" style="color:var(--white);margin-top:6px">ELECTRICAL CONTRACTORS</div>
</div>
<div class="abs contact-info" style="top:4064px;font-size:22px;line-height:31px">
  12 Alder Row<br>Kettleford NH 03000<br>1-555-014-2290<br>hello@brisket-vane.example
</div>
<a class="abs" style="left:153px;top:4225px;width:189px;height:55px;border:2px solid #fff;color:#fff;font-family:'Outfit',sans-serif;font-weight:500;font-size:20px;display:flex;align-items:center;justify-content:center">Location Map</a>

<!-- FOOTER -->
<footer class="abs footer"></footer>
<div class="abs brand" style="left:40px;width:306px;top:4480px">
  <span class="brand-mark"></span>
  <div class="brand-name" style="font-size:28px;margin-top:18px">BRISKET &amp; VANE</div>
  <div class="brand-tag" style="margin-top:4px">ELECTRICAL CONTRACTORS</div>
  <div style="font-family:'Figtree',sans-serif;font-weight:400;font-size:12px;color:#bdbdc2;margin-top:22px;line-height:22px">Copyright © 2025 Company Name<br>All Rights Reserved.</div>
</div>
<div class="abs foot-col" style="left:386px">
  <h4>QUICK LINKS</h4>
  Home<br>About Us<br>Services<br>Projects<br>News and Events<br>Contact Us
</div>
<div class="abs foot-col" style="left:616px">
  <h4>SERVICES</h4>
  Residential Services<br>Commercial Services<br>Industrial Services<br>Design &amp; Installation<br>Maintenance &amp; Support
</div>
<div class="abs foot-col" style="left:883px">
  <h4>CONTACT US</h4>
  <span style="line-height:22px;display:block;margin-top:4px">12 Alder Row<br>Kettleford NH 03000</span>
  1-555-014-2290<br>hello@brisket-vane.example
</div>
<div class="abs social" aria-label="Social links"><span></span><span></span><span></span><span></span><span></span></div>

</body>
</html>
```